Change of trading name, rebrand

existing website to be updated with new theme and logo. existing website is
www.harlowbrentmere.com.au
Industry/Entity Type
Construction
Coding
Coded - Design and coding required
Number of Pages Required
5+ page
Requirements
Must have
- be mobile phone friendly

```html
<!DOCTYPE html>
<html lang="en">
<head>
<meta charset="utf-8">
<meta name="viewport" content="width=device-width, initial-scale=1">
<title>Brentmere Plant Hire</title>
<link href="https://fonts.googleapis.com/css2?family=Roboto:wght@300;400;500;700&family=Russo+One&family=Audiowide&display=swap" rel="stylesheet">
<style>
:root{
  --navy:#2b2f86;
  --navy-deep:#23265f;
  --navy-band:#2a2d78;
  --ink:#1d1d2b;
  --grey:#6b6b78;
  --line:#b9bacb;
  --soft:#e7ebf5;
  --footer:#15151d;
  --white:#ffffff;
}
*{box-sizing:border-box;margin:0;padding:0}
html,body{width:1200px;height:3811px;overflow:hidden}
body{position:relative;font-family:'Roboto',sans-serif;color:var(--ink);background:var(--white)}
.abs{position:absolute}
a{color:inherit;text-decoration:none}

/* top bar + nav */
.topbar{left:0;top:0;width:1200px;height:40px;background:var(--navy-deep);z-index:3;color:#fff;font-size:14px}
.topbar .socials{left:402px;top:8px;display:flex;gap:7px}
.social-dot{width:24px;height:24px;border-radius:50%;background:#fff;display:block}
.topbar .sep{top:0;width:1px;height:40px;background:rgba(255,255,255,.3)}
.topbar .info{top:11px;display:flex;align-items:center;gap:8px;white-space:nowrap}
.topbar b{font-weight:700}
.brand-box{left:111px;top:0;width:154px;height:112px;background:#fff;z-index:4;display:flex;flex-direction:column;align-items:center;justify-content:center;gap:4px;color:var(--navy)}
.brand-box .mark{width:22px;height:22px;background:var(--navy);border-radius:50%}
.brand-box span{font-weight:700;font-size:15px;letter-spacing:1px;text-align:center;line-height:1.15}
.nav{left:326px;top:66px;display:flex;gap:0;z-index:3;white-space:nowrap}
.nav a{color:#fff;font-size:14px;font-weight:500;padding:6px 10px;margin-right:4px}
.nav a.active{background:var(--navy)}

/* hero */
.hero{left:0;top:0;width:1200px;height:597px;background:linear-gradient(180deg,#3f7fc4 0%,#7fb2e0 45%,#b9cfe2 70%,#c9b89a 100%)}
.hero-photo{left:480px;top:40px;width:720px;height:557px;background:linear-gradient(160deg,rgba(230,150,30,.0) 0%,rgba(232,150,25,.55) 45%,rgba(190,120,40,.35) 100%)}
.hero-text{left:111px;top:222px;color:#fff}
.hero-text .welcome{font-size:24px;font-weight:400;letter-spacing:.5px}
.hero-text .big{display:flex;align-items:flex-end;gap:8px;margin-top:6px;white-space:nowrap}
.hero-text .big strong{font-family:'Russo One',sans-serif;font-size:100px;line-height:.95;font-style:italic}
.hero-text .big span{font-size:26px;margin-bottom:6px}
.hero-text p{font-size:15px;line-height:1.5;margin-top:18px;width:340px}
.btn{display:inline-flex;align-items:center;gap:10px;border:2px solid currentColor;padding:4px 4px 4px 8px;font-size:15px;font-weight:500;white-space:nowrap}
.btn .arrow{width:42px;height:34px;display:flex;align-items:center;justify-content:center}
.hero-text .btn{margin-top:26px;color:#fff}
.hero-text .btn .arrow{background:#fff}
.dots{left:35px;top:305px;display:flex;flex-direction:column;gap:7px}
.dots i{width:11px;height:11px;border:1.5px solid #fff;border-radius:50%;display:block}
.dots i.on{background:#fff}

/* section titles */
.title{font-family:'Russo One',sans-serif;font-style:italic;font-size:32px;color:var(--navy);letter-spacing:1px;white-space:nowrap}
.title .ghost{color:transparent;-webkit-text-stroke:1.3px var(--navy);opacity:.75}
.title-bar{width:64px;height:5px;background:var(--navy)}

/* about */
.about-frame{left:136px;top:687px;width:396px;height:426px;border:2px solid var(--navy);padding:8px}
.about-photo{width:100%;height:100%;background:linear-gradient(135deg,#7a6850 0%,#c97a3a 35%,#3f5a9a 60%,#b9b7b0 100%)}
.about-copy{left:643px;top:705px;width:448px}
.about-copy .title-bar{margin-top:8px}
.about-copy h3{font-family:'Audiowide',sans-serif;font-size:16px;line-height:1.55;margin-top:36px;color:var(--ink)}
.about-copy p{font-size:15px;line-height:1.9;color:var(--grey);margin-top:18px;text-align:justify}
.about-copy .btn{margin-top:24px;color:var(--navy);border-color:var(--navy)}
.about-copy .btn span:first-child{color:var(--ink)}
.about-copy .btn .arrow{background:var(--navy)}

/* services */
.services{left:0;top:1203px;width:1200px;height:590px;background:linear-gradient(180deg,#e3e9f6 0%,#eef1f7 60%,#c9ccd6 100%)}
.services .head{left:0;top:54px;width:1200px;display:flex;flex-direction:column;align-items:center;gap:14px}
.card{top:164px;width:306px;height:335px}
.card-photo{width:100%;height:100%;background:linear-gradient(180deg,#b7c8dc 0%,#d9b43a 45%,#6c6a5e 100%)}
.card-label{background:#fff;font-size:17px;font-weight:500;padding:0;height:60px;display:flex;align-items:center;justify-content:center;width:201px}
.card-focus{background:rgba(43,47,134,.93);color:#fff;text-align:center;display:flex;flex-direction:column;align-items:center;justify-content:center;padding:0 28px}
.card-focus h4{font-size:18px;font-weight:700;margin-bottom:14px}
.card-focus p{font-size:15px;line-height:1.6}
.card-focus a{font-size:14px;font-weight:700;text-decoration:underline;margin-top:8px}
.slide-btn{top:310px;width:34px;height:34px;border-radius:50%;display:flex;align-items:center;justify-content:center}

/* partners */
.partners{left:0;top:1793px;width:1200px;height:174px;background:var(--navy-band);display:flex;align-items:center;justify-content:space-between}
.partner{height:44px;background:rgba(255,255,255,.9);border-radius:6px}

/* why */
.why-head{left:0;top:2046px;width:1200px;display:flex;flex-direction:column;align-items:center;gap:16px}
.why-item{font-size:19px;font-weight:500;line-height:1.3;color:var(--ink);white-space:nowrap;z-index:2}
.why-icon{width:72px;height:72px;border-radius:50%;background:var(--navy);border:5px solid #d6d8ea;display:flex;align-items:center;justify-content:center;z-index:2}
.why-center{left:470px;top:2400px;width:260px;text-align:center;color:var(--navy)}
.why-center .mark{width:40px;height:40px;border-radius:50%;background:var(--navy);margin:0 auto 10px}
.why-center span{font-weight:700;font-size:24px;letter-spacing:1px;line-height:1.2}

/* cta */
.cta{left:0;top:2573px;width:1200px;height:263px;background:var(--navy-band)}
.cta h2{left:111px;top:82px;font-family:'Audiowide',sans-serif;font-style:italic;color:#fff;font-size:36px;line-height:1.4;letter-spacing:1px;white-space:nowrap}
.cta .btn{left:929px;top:109px;color:#fff;font-size:15px}
.cta .btn .arrow{background:transparent;border-left:2px solid #fff}

/* contact */
.footer-bg{left:0;top:3236px;width:1200px;height:575px;background:var(--footer)}
.map{left:111px;top:2925px;width:440px;height:378px;border:2px solid var(--navy);background:linear-gradient(135deg,#e8eaee 0%,#dfe6d9 50%,#e6e3da 100%)}
.form-card{left:380px;top:2952px;width:659px;height:406px;background:#fff;box-shadow:0 6px 24px rgba(0,0,0,.12)}
.form-card .title{left:0;top:55px;width:659px;text-align:center}
.form-card .title-bar{left:297px;top:104px}
.field{font-size:14px;color:#8d8d99;border-bottom:1px solid #8d8d99;padding-bottom:4px}
.form-card .btn{left:257px;top:328px;color:var(--navy);font-size:14px}
.form-card .btn span:first-child{color:var(--ink)}
.form-card .btn .arrow{background:var(--navy);height:32px}

/* footer */
.foot-brand{left:111px;top:3455px;width:218px;text-align:center;color:#fff}
.foot-brand .mark{width:44px;height:44px;border-radius:50%;background:#fff;margin:0 auto 12px}
.foot-brand span{font-weight:700;font-size:24px;letter-spacing:1.5px;line-height:1.2}
.foot h5{font-size:17px;font-weight:500;color:#fff;letter-spacing:.3px}
.foot ul{list-style:none;margin-top:20px}
.foot li{font-size:14px;color:#fff;height:35px;padding-left:2px;white-space:nowrap}
.contact-row{display:flex;gap:14px;align-items:flex-start;color:#fff}
.contact-row .ic{width:42px;height:42px;border-radius:50%;background:#fff;display:flex;align-items:center;justify-content:center;flex:none}
.contact-row strong{font-size:19px;font-weight:500;display:block}
.contact-row small{font-size:14px;line-height:1.6;display:block;white-space:nowrap}
.foot-social{display:flex;gap:8px;margin-top:18px}
.foot-social i{width:44px;height:44px;border-radius:50%;border:2px solid #fff;background:#fff;display:block}
.copyright{left:0;top:3762px;width:1200px;text-align:center;color:#fff;font-size:15px}
</style>
</head>
<body>

<!-- HERO -->
<section class="hero abs">
  <div class="hero-photo abs" role="img" aria-label="Orange excavator on a dirt mound under a blue sky"></div>
  <div class="dots abs"><i></i><i class="on"></i><i></i></div>
  <div class="hero-text abs">
    <div class="welcome">WELCOME TO</div>
    <div class="big"><strong>HBP</strong><span>PLANT HIRE</span></div>
    <p>Lorem ipsum dolor sit amet, consectetur ipiscing elit, sed do eiusmod tempor.</p>
    <a class="btn" href="#"><span>GET STARTED</span><span class="arrow"><svg width="24" height="16" viewBox="0 0 24 16"><path d="M1 8h21M15 1l7 7-7 7" fill="none" stroke="#1d1d2b" stroke-width="2"/></svg></span></a>
  </div>
</section>

<div class="topbar abs">
  <div class="socials abs"><span class="social-dot"></span><span class="social-dot"></span><span class="social-dot"></span></div>
  <span class="sep abs" style="left:540px"></span>
  <div class="info abs" style="left:591px"><svg width="15" height="15" viewBox="0 0 24 24"><path d="M6.6 10.8a15 15 0 006.6 6.6l2.2-2.2a1 1 0 011-.25 11.4 11.4 0 003.6.6 1 1 0 011 1V20a1 1 0 01-1 1A17 17 0 013 4a1 1 0 011-1h3.5a1 1 0 011 1c0 1.25.2 2.45.6 3.6a1 1 0 01-.25 1z" fill="#fff"/></svg><span><b>Phone No:</b> 1300 555 014</span></div>
  <span class="sep abs" style="left:839px"></span>
  <div class="info abs" style="left:879px"><svg width="15" height="12" viewBox="0 0 24 18"><path d="M0 0h24v18H0z" fill="#fff"/><path d="M0 0l12 9 12-9" fill="none" stroke="#23265f" stroke-width="2"/></svg><span><b>Mail:</b> info@brentmereplant.com.au</span></div>
</div>

<div class="brand-box abs"><span class="mark"></span><span>BRENTMERE<br>PLANT HIRE</span></div>

<nav class="nav abs">
  <a class="active" href="#">HOME</a><a href="#">ABOUT US</a><a href="#">PLANT HIRE</a><a href="#">MAJOR PROJECT SNAPSHOT</a><a href="#">POLICIES</a><a href="#">JOBS</a><a href="#">CONTACT US</a>
</nav>

<!-- ABOUT -->
<div class="about-frame abs"><div class="about-photo" role="img" aria-label="Company owner standing beside an orange excavator attachment and a work ute"></div></div>
<div class="about-copy abs">
  <div class="title">ABOUT <span class="ghost">US</span></div>
  <div class="title-bar"></div>
  <h3>HBP Heavy Equipment Hire Committed to Superior Quality Plant Hire Services.</h3>
  <p>Harlow Brentmere Heavy Equipment Hire specialise in the hire of heavy earthmoving, mining and construction machines with specialised attachments and tooling. Our array of machines and attachments is second to none, and we have one of the largest hire fleets available in South East Queensland.</p>
  <a class="btn" href="#"><span>READ MORE</span><span class="arrow"><svg width="24" height="16" viewBox="0 0 24 16"><path d="M1 8h21M15 1l7 7-7 7" fill="none" stroke="#fff" stroke-width="2"/></svg></span></a>
</div>

<!-- SERVICES -->
<section class="services abs">
  <div class="head abs"><div class="title">OUR <span class="ghost">SERVICES</span></div><div class="title-bar"></div></div>
  <div class="slide-btn abs" style="left:51px;background:#111"><svg width="12" height="14" viewBox="0 0 12 14"><path d="M9 1L3 7l6 6" fill="none" stroke="#fff" stroke-width="2.5"/></svg></div>
  <div class="slide-btn abs" style="left:1114px;border:1.5px solid #111"><svg width="12" height="14" viewBox="0 0 12 14"><path d="M3 1l6 6-6 6" fill="none" stroke="#111" stroke-width="2"/></svg></div>
  <div class="card abs" style="left:113px"><div class="card-photo" role="img" aria-label="Yellow articulated water cart truck"></div><div class="card-label abs" style="left:-2px;top:281px">WATER CARTS</div></div>
  <div class="card card-focus abs" style="left:447px">
    <h4>DUMP TRUCKS</h4>
    <p>We are South East Queensland's material cartage and haulage specialists, with a range</p>
    <a href="#">READ MORE</a>
    <svg class="abs" style="left:259px;top:300px" width="24" height="12" viewBox="0 0 24 12"><path d="M0 6h22M17 1l5 5-5 5" fill="none" stroke="#fff" stroke-width="2"/></svg>
  </div>
  <div class="card abs" style="left:782px"><div class="card-photo" role="img" aria-label="Yellow skid steer bobcat in a yard"></div><div class="card-label abs" style="left:-2px;top:282px">BOBCATS</div></div>
</section>

<!-- PARTNERS -->
<section class="partners abs" aria-label="Partners">
  <span class="partner" style="width:110px;margin-left:-10px"></span>
  <span class="partner" style="width:180px"></span>
  <span class="partner" style="width:268px"></span>
  <span class="partner" style="width:174px"></span>
  <span class="partner" style="width:140px;margin-right:-10px"></span>
</section>

<!-- WHY -->
<div class="why-head abs"><div class="title">WHY CHOOSE <span class="ghost">HBP</span></div><div class="title-bar"></div></div>
<svg class="abs" style="left:0;top:2260px" width="1200" height="313" viewBox="0 0 1200 313">
  <path d="M280 313 A320 320 0 0 1 920 313" fill="none" stroke="#b9bacb" stroke-width="1.5" stroke-dasharray="4 4"/>
  <path d="M372 313 A228 228 0 0 1 828 313" fill="none" stroke="#2b2f86" stroke-width="7"/>
  <path d="M392 313 A208 208 0 0 1 808 313" fill="none" stroke="#e6e7f0" stroke-width="10"/>
</svg>
<div class="why-item abs" style="left:450px;top:2168px;width:300px;text-align:center">ONE OF QLD'S LARGEST<br>SUPPLIERS</div>
<div class="why-icon abs" style="left:564px;top:2229px"><svg width="30" height="30" viewBox="0 0 24 24"><path d="M4 20h16M6 20l3-12 4 3 5-7v16" fill="none" stroke="#fff" stroke-width="1.6"/></svg></div>
<div class="why-item abs" style="left:136px;top:2341px;width:200px;text-align:right">100+MACHINES<br>IN FLEET</div>
<div class="why-icon abs" style="left:349px;top:2329px"><svg width="30" height="30" viewBox="0 0 24 24"><path d="M3 19h12v-4H3zM9 15l5-8 6 4-2 4" fill="none" stroke="#fff" stroke-width="1.6"/></svg></div>
<div class="why-item abs" style="left:74px;top:2488px;width:200px;text-align:right">20+YEARS OF<br>EXPERIENCE</div>
<div class="why-icon abs" style="left:289px;top:2474px"><svg width="30" height="30" viewBox="0 0 24 24"><circle cx="12" cy="10" r="6" fill="none" stroke="#fff" stroke-width="1.6"/><path d="M8 15l-2 7 6-3 6 3-2-7" fill="none" stroke="#fff" stroke-width="1.6"/></svg></div>
<div class="why-icon abs" style="left:756px;top:2311px"><svg width="30" height="30" viewBox="0 0 24 24"><path d="M4 20h16V10H4zM9 10V5h6v5" fill="none" stroke="#fff" stroke-width="1.6"/></svg></div>
<div class="why-item abs" style="left:839px;top:2334px">ONSITE SERVICING</div>
<div class="why-icon abs" style="left:832px;top:2471px"><svg width="30" height="30" viewBox="0 0 24 24"><path d="M6 3h12M12 3v18M8 8h8" fill="none" stroke="#fff" stroke-width="1.6"/></svg></div>
<div class="why-item abs" style="left:917px;top:2484px">CUSTOM MACHINE<br>ATTACHMENTS</div>
<div class="why-center abs"><div class="mark"></div><span>BRENTMERE<br>PLANT HIRE</span></div>

<!-- CTA -->
<section class="cta abs">
  <h2 class="abs">Contact us today for a<br>free quote</h2>
  <a class="btn abs" href="#"><span>GET A QUOTE</span><span class="arrow"><svg width="24" height="16" viewBox="0 0 24 16"><path d="M1 8h21M15 1l7 7-7 7" fill="none" stroke="#fff" stroke-width="2"/></svg></span></a>
</section>

<!-- CONTACT -->
<div class="footer-bg abs"></div>
<div class="map abs" role="img" aria-label="Street map showing the yard location"></div>
<div class="form-card abs">
  <div class="title abs">CONTACT <span class="ghost">US</span></div>
  <div class="title-bar abs"></div>
  <div class="field abs" style="left:49px;top:145px;width:265px">First Name</div>
  <div class="field abs" style="left:349px;top:145px;width:264px">Last Name</div>
  <div class="field abs" style="left:49px;top:212px;width:265px">Email Address</div>
  <div class="field abs" style="left:349px;top:212px;width:264px">Phone No</div>
  <div class="field abs" style="left:47px;top:273px;width:566px">Text Here</div>
  <a class="btn abs" href="#"><span>SUBMIT NOW</span><span class="arrow"><svg width="24" height="16" viewBox="0 0 24 16"><path d="M1 8h21M15 1l7 7-7 7" fill="none" stroke="#fff" stroke-width="2"/></svg></span></a>
</div>

<!-- FOOTER -->
<div class="foot-brand abs"><div class="mark"></div><span>BRENTMERE<br>PLANT HIRE</span></div>
<div class="foot abs" style="left:424px;top:3437px">
  <h5>QUICK LINKS</h5>
  <ul><li>Home</li><li>About Us</li><li>Plant Hire</li><li>Major Project Snapshot</li><li>Policies</li><li>Jobs</li><li>Contact Us</li></ul>
</div>
<div class="foot abs" style="left:664px;top:3437px">
  <h5>CONTACT US</h5>
  <div class="contact-row" style="margin-top:24px"><span class="ic"><svg width="20" height="15" viewBox="0 0 24 18"><path d="M0 0h24v18H0z" fill="#15151d"/><path d="M0 0l12 9 12-9" fill="none" stroke="#fff" stroke-width="2"/></svg></span><div><strong>Email:</strong><small>info@brentmereplant.com.au</small></div></div>
  <div class="contact-row" style="margin-top:30px"><span class="ic"><svg width="20" height="20" viewBox="0 0 24 24"><path d="M6.6 10.8a15 15 0 006.6 6.6l2.2-2.2a1 1 0 011-.25 11.4 11.4 0 003.6.6 1 1 0 011 1V20a1 1 0 01-1 1A17 17 0 013 4a1 1 0 011-1h3.5a1 1 0 011 1c0 1.25.2 2.45.6 3.6a1 1 0 01-.25 1z" fill="#15151d"/></svg></span><div><strong>Phone No:</strong><small>1300 555 014</small></div></div>
  <div class="contact-row" style="margin-top:30px"><span class="ic"><svg width="18" height="22" viewBox="0 0 18 24"><path d="M9 0a9 9 0 019 9c0 7-9 15-9 15S0 16 0 9a9 9 0 019-9z" fill="#15151d"/><circle cx="9" cy="9" r="3.5" fill="#fff"/></svg></span><div><strong>Location:</strong><small>18 Wattlegum Rd, Kestrel Vale<br>QLD 4199</small></div></div>
</div>
<div class="foot abs" style="left:940px;top:3437px">
  <h5>FOLLOW US</h5>
  <div class="foot-social"><i></i><i></i><i></i></div>
</div>
<div class="copyright abs">Copyright © 2024 Brentmere Plant Hire | All Rights Reserved</div>

</body>
</html>
```